I have an animal hospital. I want a poster to hang in each exam room to show a picture of a normal sized heart and then an enlarged heart of a dog that was fed a grain-free diet. I want to warn people not to feed grain-free diets. Maybe at the top of the poster, "Do you feed grain-free?" and then the x-ray comparison, then the warnings of Canine Dilated Cardiomyopathy.

```html
<!DOCTYPE html>
<html lang="en">
<head>
<meta charset="UTF-8">
<title>Do You Feed Grain-Free? – Exam Room Poster</title>
<link href="https://fonts.googleapis.com/css2?family=Barlow+Semi+Condensed:wght@600;700;800&family=Montserrat:wght@500;600;700&display=swap" rel="stylesheet">
<style>
  :root {
    --lime: #c3d14a;
    --olive: #5b6720;
    --charcoal: #3b3b3b;
    --white: #ffffff;
    --ink: #2b2b2b;
    --alert-red: #e12b2b;
    --heart-deep: #9e1f24;
    --heart-light: #e9837d;
  }
  * { margin: 0; padding: 0; box-sizing: border-box; }
  html, body { width: 890px; height: 1200px; overflow: hidden; background: #f1f1f1; }
  .poster {
    position: relative;
    width: 890px;
    height: 1200px;
    overflow: hidden;
    background: var(--charcoal);
    font-family: "Montserrat", Arial, sans-serif;
  }
  .backdrop { position: absolute; inset: 0; }

  .headline {
    position: absolute;
    left: 0; right: 0;
    text-align: center;
    font-family: "Barlow Semi Condensed", "Arial Narrow", sans-serif;
    color: var(--ink);
    text-transform: uppercase;
    line-height: 1;
  }
  .headline-lead { top: 43px; font-size: 62px; font-weight: 700; letter-spacing: -0.5px; }
  .headline-main { top: 90px; font-size: 96px; font-weight: 800; letter-spacing: -0.5px; }
  .headline-rule {
    position: absolute; left: 161px; top: 190px; width: 565px; height: 1px;
    background: rgba(43,43,43,0.35);
  }

  .heart-label {
    position: absolute; top: 201px;
    font-size: 18px; line-height: 22px; font-weight: 500; color: var(--ink);
    transform: translateX(-50%); white-space: nowrap;
  }
  .heart-label.normal { left: 260px; }
  .heart-label.dilated { left: 573px; }

  .heart-art {
    position: absolute; top: 230px; height: 318px;
    border-radius: 46% 46% 50% 50% / 40% 40% 60% 60%;
    background: radial-gradient(ellipse at 50% 55%, var(--heart-deep) 0%, #c24a4a 55%, var(--heart-light) 100%);
    box-shadow: 0 18px 18px -12px rgba(0,0,0,0.35);
  }
  .heart-art.normal { left: 150px; width: 280px; }
  .heart-art.dilated { left: 448px; width: 305px; }

  .section-title {
    position: absolute; top: 549px; left: 0; right: 0;
    text-align: center;
    font-family: "Barlow Semi Condensed", "Arial Narrow", sans-serif;
    font-weight: 700; font-size: 38px; color: var(--ink);
    text-transform: uppercase; letter-spacing: 0.2px;
  }

  .xray {
    position: absolute; top: 607px; height: 304px;
    border: 3px solid var(--white);
    border-radius: 16px;
    overflow: hidden;
    background: #000;
    box-shadow: 0 0 0 1px rgba(0,0,0,0.25);
  }
  .xray.with-grain { left: 96px; width: 375px; }
  .xray.grain-free { left: 521px; width: 273px; }
  .xray-film {
    position: absolute; inset: 0;
    background: radial-gradient(ellipse 38% 60% at 50% 55%, #d9d9d9 0%, #8a8a8a 40%, #2a2a2a 75%, #050505 100%);
  }
  .xray-caption {
    position: absolute; left: 0; right: 0; bottom: 0; height: 48px;
    background: rgba(91,103,32,0.92);
    color: #e9ecd6; font-size: 19px; font-weight: 500;
    display: flex; align-items: center; justify-content: center;
  }

  .warning-badge { position: absolute; left: 156px; top: 930px; width: 100px; height: 100px; }
  .warning-title {
    position: absolute; left: 273px; top: 940px;
    font-family: "Barlow Semi Condensed", "Arial Narrow", sans-serif;
    font-weight: 700; font-size: 38px; line-height: 42px; text-transform: uppercase;
  }
  .warning-title .line-one { display: block; color: var(--white); }
  .warning-title .line-two { display: block; color: var(--lime); }

  .symptom-list { position: absolute; top: 1043px; list-style: none; }
  .symptom-list.left { left: 113px; }
  .symptom-list.right { left: 551px; }
  .symptom-list li {
    display: flex; align-items: center; gap: 10px;
    height: 29.5px;
    color: var(--white); font-size: 20px; font-weight: 600; letter-spacing: 0.3px;
  }
  .tick { width: 19px; height: 19px; flex: none; }

  .footer-bar { position: absolute; left: 0; right: 0; bottom: 0; height: 20px; background: var(--lime); }
</style>
</head>
<body>
<main class="poster">
  <svg class="backdrop" width="890" height="1200" viewBox="0 0 890 1200" aria-hidden="true">
    <rect width="890" height="1200" fill="var(--charcoal)"/>
    <circle cx="445" cy="272" r="345" fill="var(--lime)"/>
    <path fill="var(--lime)" d="M0 430 Q20 418 40 430 T80 430 T120 430 T160 430 T200 430 T240 430 T280 430 T320 430 T360 430 T400 430 T440 430 T480 430 T520 430 T560 430 T600 430 T640 430 T680 430 T720 430 T760 430 T800 430 T840 430 T880 430 T920 430 V480 H0 Z"/>
    <path fill="var(--white)" d="M0 442 Q20 430 40 442 T80 442 T120 442 T160 442 T200 442 T240 442 T280 442 T320 442 T360 442 T400 442 T440 442 T480 442 T520 442 T560 442 T600 442 T640 442 T680 442 T720 442 T760 442 T800 442 T840 442 T880 442 T920 442 L920 795 Q890 775 860 795 T800 795 T740 795 T680 795 T620 795 T560 795 T500 795 T440 795 T380 795 T320 795 T260 795 T200 795 T140 795 T80 795 T20 795 T-40 795 Z"/>
    <path fill="none" stroke="var(--lime)" stroke-width="3" d="M236 569 H75 Q61 569 61 583 V780"/>
    <path fill="none" stroke="var(--lime)" stroke-width="3" d="M652 569 H816 Q830 569 830 583 V780"/>
  </svg>

  <h1 class="headline headline-lead">Do you feed</h1>
  <h1 class="headline headline-main">Grain-free?</h1>
  <div class="headline-rule"></div>

  <span class="heart-label normal">Normal</span>
  <span class="heart-label dilated">Dilated Cardiomyopathy</span>
  <div class="heart-art normal" role="img" aria-label="Anatomical cross-section illustration of a normal canine heart"></div>
  <div class="heart-art dilated" role="img" aria-label="Anatomical cross-section illustration of an enlarged heart with dilated cardiomyopathy"></div>

  <h2 class="section-title">X-Ray Comparison</h2>

  <figure class="xray with-grain">
    <div class="xray-film" role="img" aria-label="Chest x-ray of a dog on a grain diet showing a normal sized heart"></div>
    <figcaption class="xray-caption">With grain diet</figcaption>
  </figure>
  <figure class="xray grain-free">
    <div class="xray-film" role="img" aria-label="Chest x-ray of a dog on a grain-free diet showing an enlarged heart"></div>
    <figcaption class="xray-caption">Grain free diet</figcaption>
  </figure>

  <svg class="warning-badge" viewBox="0 0 100 100" aria-hidden="true">
    <circle cx="50" cy="50" r="50" fill="var(--lime)"/>
    <path d="M50 18 L82 74 Q84 79 79 79 H21 Q16 79 18 74 Z" fill="var(--alert-red)" stroke="var(--white)" stroke-width="4" stroke-linejoin="round"/>
    <rect x="46" y="36" width="8" height="26" rx="3" fill="var(--white)"/>
    <circle cx="50" cy="70" r="4.5" fill="var(--white)"/>
  </svg>
  <h2 class="warning-title">
    <span class="line-one">Warnings of canine</span>
    <span class="line-two">Dilated cardiomyopathy</span>
  </h2>

  <ul class="symptom-list left">
    <li><svg class="tick" viewBox="0 0 20 20"><circle cx="10" cy="10" r="10" fill="var(--lime)"/><path d="M5.5 10.5 L8.8 13.5 L14.5 7" fill="none" stroke="var(--charcoal)" stroke-width="2.4" stroke-linecap="round" stroke-linejoin="round"/></svg>Coughing or gagging</li>
    <li><svg class="tick" viewBox="0 0 20 20"><circle cx="10" cy="10" r="10" fill="var(--lime)"/><path d="M5.5 10.5 L8.8 13.5 L14.5 7" fill="none" stroke="var(--charcoal)" stroke-width="2.4" stroke-linecap="round" stroke-linejoin="round"/></svg>Weakness</li>
    <li><svg class="tick" viewBox="0 0 20 20"><circle cx="10" cy="10" r="10" fill="var(--lime)"/><path d="M5.5 10.5 L8.8 13.5 L14.5 7" fill="none" stroke="var(--charcoal)" stroke-width="2.4" stroke-linecap="round" stroke-linejoin="round"/></svg>Reduced ability to exercise</li>
    <li><svg class="tick" viewBox="0 0 20 20"><circle cx="10" cy="10" r="10" fill="var(--lime)"/><path d="M5.5 10.5 L8.8 13.5 L14.5 7" fill="none" stroke="var(--charcoal)" stroke-width="2.4" stroke-linecap="round" stroke-linejoin="round"/></svg>Collapse or fainting</li>
  </ul>
  <ul class="symptom-list right">
    <li><svg class="tick" viewBox="0 0 20 20"><circle cx="10" cy="10" r="10" fill="var(--lime)"/><path d="M5.5 10.5 L8.8 13.5 L14.5 7" fill="none" stroke="var(--charcoal)" stroke-width="2.4" stroke-linecap="round" stroke-linejoin="round"/></svg>Decreased appetite</li>
    <li><svg class="tick" viewBox="0 0 20 20"><circle cx="10" cy="10" r="10" fill="var(--lime)"/><path d="M5.5 10.5 L8.8 13.5 L14.5 7" fill="none" stroke="var(--charcoal)" stroke-width="2.4" stroke-linecap="round" stroke-linejoin="round"/></svg>Weight loss</li>
    <li><svg class="tick" viewBox="0 0 20 20"><circle cx="10" cy="10" r="10" fill="var(--lime)"/><path d="M5.5 10.5 L8.8 13.5 L14.5 7" fill="none" stroke="var(--charcoal)" stroke-width="2.4" stroke-linecap="round" stroke-linejoin="round"/></svg>Distended belly</li>
    <li><svg class="tick" viewBox="0 0 20 20"><circle cx="10" cy="10" r="10" fill="var(--lime)"/><path d="M5.5 10.5 L8.8 13.5 L14.5 7" fill="none" stroke="var(--charcoal)" stroke-width="2.4" stroke-linecap="round" stroke-linejoin="round"/></svg>Sudden death</li>
  </ul>

  <div class="footer-bar"></div>
</main>
</body>
</html>
```